Brightwick Music Studio needs a promotional postcard design

We are looking for a postcard design for a small business that provides clients with private music lesson instruction. We are looking for a design that will convey the message of "music is fun for kids" that will appeal to parents and encourage them to sign up. We have a company logo that should be used and our color scheme is teal and turquoise. All of our contact info should be displayed as well.

Target Market(s)

Parents with young kids

Contact Information for Business Card

web: www.brightwickmusicstudio.example
email: lessons@brightwickmusicstudio.example
phone: 202-555-0147

Font styles to use
Serif
Sans Serif

Colors
33b8a4
86cfc6
0456a4
87cfc6

Requirements
Must have
• Music lessons in your home
• Creating little stars one at a time
• Sign Up Now
• Please use these images:
Nice to have
• Something like this sample postcard:

```html
<!DOCTYPE html>
<html lang="en">
<head>
<meta charset="utf-8">
<title>Brightwick Music Studio – Postcard</title>
<link rel="stylesheet" href="https://fonts.googleapis.com/css2?family=Cormorant+Garamond:wght@500&family=Mystery+Quest&family=Oswald:wght@400;600&display=swap">
<style>
  :root {
    --teal: #4fb7bc;
    --ink: #0d0d0e;
    --paper: #ffffff;
    --stage: #2b2b2d;
    --rule: #c9c9c9;
  }
  * { box-sizing: border-box; margin: 0; padding: 0; }
  html, body { width: 1200px; height: 698px; overflow: hidden; background: var(--stage); }
  .stage { position: relative; width: 1200px; height: 698px; }

  .card { position: absolute; top: 149px; width: 480px; height: 400px; overflow: hidden; }
  .card--front { left: 105px; background: var(--ink); }
  .card--back { left: 616px; background: var(--teal); }

  .brand-name {
    font-family: "Cormorant Garamond", serif;
    font-weight: 500;
    line-height: 1;
  }

  /* front */
  .front-mark {
    position: absolute; left: 29px; top: 22px; width: 71px; height: 71px;
    border-radius: 50%; background: var(--teal);
  }
  .front-brand { position: absolute; left: 119px; top: 28px; color: var(--teal); }
  .front-brand .brand-title { font-size: 37px; display: block; }
  .front-brand .brand-sub { font-size: 13px; letter-spacing: 5px; display: block; margin-top: 8px; }

  .front-photo {
    position: absolute; left: 168px; top: 58px; width: 312px; height: 282px;
    background: radial-gradient(ellipse at 60% 40%, #8a6a56 0%, #3a3236 45%, #1d1c22 80%, var(--ink) 100%);
    border-radius: 140px 0 0 40px;
  }
  .front-wave { position: absolute; left: 0; top: 0; width: 480px; height: 400px; }
  .tagline {
    position: absolute; left: 32px; top: 283px;
    font-family: "Mystery Quest", cursive; font-size: 38px; line-height: 52px; color: var(--ink);
    white-space: nowrap;
  }

  /* back */
  .back-shape { position: absolute; left: 0; top: 0; width: 480px; height: 400px; }
  .back-mark {
    position: absolute; left: 66px; top: 40px; width: 60px; height: 60px;
    border-radius: 50%; background: var(--paper);
  }
  .back-brand { position: absolute; left: 0; width: 193px; top: 128px; text-align: center; color: var(--paper); }
  .back-brand .brand-title { font-size: 32px; display: block; }
  .back-brand .brand-sub { font-size: 12px; letter-spacing: 4.5px; display: block; margin-top: 8px; }

  .back-photo {
    position: absolute; left: 52px; top: 201px; width: 108px; height: 122px;
    background: linear-gradient(180deg, #3a2a22 0%, #d1312c 30%, #c02a27 70%, #2a2a2a 100%);
    border-radius: 40px 40px 6px 6px;
  }
  .contact { position: absolute; left: 0; width: 193px; top: 323px; text-align: center; color: var(--paper); font-family: "Oswald", sans-serif; }
  .contact-phone {
    display: inline-block; font-weight: 600; font-size: 21px; line-height: 26px;
    padding: 1px 2px; border-top: 1.5px solid var(--paper); border-bottom: 1.5px solid var(--paper);
  }
  .contact-line { display: block; font-size: 9.5px; line-height: 14px; text-transform: uppercase; white-space: nowrap; }
  .contact-line:first-of-type { margin-top: 5px; }

  .stamp-box { position: absolute; left: 390px; top: 37px; width: 51px; height: 50px; border: 1px solid var(--rule); }
  .address-label { position: absolute; left: 277px; top: 104px; font-family: "Oswald", sans-serif; font-size: 9px; color: var(--ink); }
  .address-line { position: absolute; left: 286px; width: 153px; height: 0; border-top: 1px solid var(--rule); }
</style>
</head>
<body>
<main class="stage">

  <section class="card card--front">
    <div class="front-photo" role="img" aria-label="Photo of a smiling young girl making a peace sign"></div>
    <svg class="front-wave" viewBox="0 0 480 400" aria-hidden="true">
      <path d="M0,262 C30,245 60,232 95,231 C160,230 230,275 300,310 C360,340 420,355 480,300 L480,400 L0,400 Z" fill="var(--teal)"/>
      <path d="M28,262 C60,242 90,238 120,241 C190,248 260,300 330,330 C380,352 440,355 480,320" fill="none" stroke="var(--ink)" stroke-width="3"/>
    </svg>
    <div class="front-mark"></div>
    <div class="front-brand brand-name">
      <span class="brand-title">Brightwick</span>
      <span class="brand-sub">MUSIC&nbsp;&nbsp;STUDIO</span>
    </div>
    <p class="tagline">music is<br>fun for kids</p>
  </section>

  <section class="card card--back">
    <svg class="back-shape" viewBox="0 0 480 400" aria-hidden="true">
      <path d="M290,0 L480,0 L480,400 L290,400 C225,385 185,330 182,260 C180,190 200,90 235,40 C250,18 268,6 290,0 Z" fill="var(--paper)"/>
    </svg>
    <div class="back-mark"></div>
    <div class="back-brand brand-name">
      <span class="brand-title">Brightwick</span>
      <span class="brand-sub">MUSIC&nbsp;&nbsp;STUDIO</span>
    </div>
    <div class="back-photo" role="img" aria-label="Photo of a young girl in a red dress dancing with a violin"></div>
    <div class="contact">
      <span class="contact-phone">202-555-0147</span>
      <span class="contact-line">lessons@brightwickmusicstudio.example</span>
      <span class="contact-line">www.brightwickmusicstudio.example</span>
    </div>
    <div class="stamp-box"></div>
    <span class="address-label">To</span>
    <div class="address-line" style="top:145px"></div>
    <div class="address-line" style="top:169px"></div>
    <div class="address-line" style="top:191px"></div>
    <div class="address-line" style="top:216px"></div>
  </section>

</main>
</body>
</html>
```